Bramwell Corner Sports Pub. Where the locals go!!

We are creating a sports pub. We are needing a fun website that offers our menu along with an event page and general info. We have some attached links that we really like:
https://www.dunmorrows.example/
https://www.cafepelindra.example/
https://www.quillstoneyx.example/
We are doing a pirate theme but that is because the area we are in. We would like to see a pirate like in our logo doing something like drinking real time similar to the dunmorrows website above.
Target Market(s)
Sports Fans
Industry/Entity Type
Pub, Bar, Restaurant
Coding
Coded - Design and coding required
Number of Pages Required
3 page
Font styles to use
Other font styles liked:
- see uploads
Look and feel

```html
<!DOCTYPE html>
<html lang="en">
<head>
<meta charset="UTF-8">
<title>Bramwell Corner Sports Pub</title>
<link rel="stylesheet" href="https://fonts.googleapis.com/css2?family=Rye&family=Poppins:wght@400;600&display=swap">
<style>
:root{
  --maroon:#5c0100;
  --maroon-deep:#4a0000;
  --tan:#a07f52;
  --cream:#ffffff;
  --ink:#1d1d1d;
  --barrel:#efe6d8;
}
*{margin:0;padding:0;box-sizing:border-box}
html,body{width:1200px;height:3541px;overflow:hidden}
body{position:relative;font-family:"Poppins",sans-serif;color:var(--ink);background:var(--cream)}
.abs{position:absolute}

/* Hero */
.hero{position:absolute;left:0;top:0;width:1200px;height:685px;
  background:radial-gradient(ellipse at 50% 40%,#8a5a2e 0%,#5e3517 45%,#3a1e0d 100%)}
.nav-bar{position:absolute;left:110px;top:30px;width:979px;height:117px;background:var(--maroon);border:1px solid #b9895a}
.nav-bar a{position:absolute;top:48px;color:#fff;text-decoration:none;font-family:"Rye",serif;font-size:17px;text-transform:uppercase;text-shadow:1px 1px 0 #000;white-space:nowrap}
.brand-badge{position:absolute;left:527px;top:4px;width:170px;height:170px;border-radius:50%;background:#fff;border:9px solid #8d6e47;
  display:flex;align-items:center;justify-content:center;text-align:center;font-family:"Rye",serif;font-size:17px;line-height:1.3;color:var(--maroon);text-transform:uppercase}
.hero-title{position:absolute;left:0;top:300px;width:1200px;text-align:center;color:#fff;font-family:"Rye",serif;font-size:50px;font-weight:400;line-height:78px;text-transform:uppercase;letter-spacing:2px;text-shadow:3px 3px 0 #3a0000,0 0 12px #000}

/* Shared */
.section-title{position:absolute;left:0;width:1200px;text-align:center;font-family:"Rye",serif;font-size:46px;font-weight:400;text-transform:uppercase;letter-spacing:2px}
.text-block{position:absolute;display:flex;flex-direction:column;align-items:flex-start}
.copy{font-size:20px;line-height:33.4px}
.btn{display:flex;align-items:center;justify-content:center;border-radius:30px;font-family:"Rye",serif;font-size:18px;text-transform:uppercase;letter-spacing:1px;text-decoration:none;flex-shrink:0}
.btn-maroon{background:var(--maroon);color:#fff}
.btn-tan{background:var(--tan);color:var(--maroon)}

/* About */
.about{position:absolute;left:0;top:685px;width:1200px;height:685px;background:var(--tan)}
.about .section-title{top:105px;color:var(--maroon)}
.about-art{position:absolute;left:55px;top:174px;width:543px;height:406px;border-radius:40px;
  background:radial-gradient(ellipse at 50% 50%,#3d4f6a 0%,#5b3b22 55%,var(--tan) 80%)}
.about-text{left:627px;top:192px;width:455px}
.about-text .copy{color:#fff}
.about-text .btn{margin-top:22px;width:218px;height:54px}

/* Menu */
.menu{position:absolute;left:0;top:1370px;width:1200px;height:811px;background:var(--maroon)}
.menu .section-title{top:100px;color:#fff}
.menu-intro{position:absolute;left:0;top:177px;width:1200px;text-align:center;color:#fff;font-size:20px;line-height:35px}
.menu-item{position:absolute;top:277px;width:244px;text-align:center;color:#fff}
.menu-photo{width:244px;height:244px;border-radius:50%}
.menu-name{margin-top:16px;font-family:"Rye",serif;font-size:23px;text-transform:uppercase;letter-spacing:1px}
.menu-price{margin-top:6px;font-weight:600;font-size:20px}
.menu .btn{position:absolute;left:491px;top:671px;width:218px;height:51px}

/* Events */
.events{position:absolute;left:0;top:2181px;width:1200px;height:895px;background:#fff;overflow:hidden}
.events .section-title{top:115px;color:var(--maroon)}
.barrel{position:absolute;background:var(--barrel);border-radius:40px}
.event-photo{position:absolute}
.event-text .copy{color:var(--ink)}
.event-text .btn{margin-top:22px;width:219px;height:52px}

/* Footer */
.footer{position:absolute;left:0;top:3076px;width:1200px;height:465px;background:radial-gradient(ellipse at 50% 50%,#6b0a06 0%,var(--maroon-deep) 70%)}
.footer-brand{position:absolute;left:0;top:175px;width:1200px;text-align:center;color:#fff;font-family:"Rye",serif;font-size:26px;text-transform:uppercase}
.footer-nav{position:absolute;left:0;top:258px;width:1200px;display:flex;justify-content:center;gap:28px}
.footer-nav a{color:#fff;text-decoration:none;font-family:"Rye",serif;font-size:17px;text-transform:uppercase}
.social{position:absolute;left:0;top:312px;width:1200px;display:flex;justify-content:center;gap:24px}
.social span{width:30px;height:30px;border:3px solid #fff;border-radius:50%}
.legal{position:absolute;left:0;top:384px;width:1200px;text-align:center;color:#fff;font-family:"Rye",serif;font-size:13px;line-height:21px;text-transform:uppercase}
</style>
</head>
<body>

<header class="hero" role="img" aria-label="Busy pub interior with guests at the bar and screens on the walls">
  <nav class="nav-bar">
    <a href="#" style="left:2px">Home</a>
    <a href="#" style="left:87px">About Us</a>
    <a href="#" style="left:219px">Services</a>
    <a href="#" style="left:678px">Event</a>
    <a href="#" style="left:776px">Contact Us</a>
    <a href="#" style="left:931px">FAQ</a>
  </nav>
  <div class="brand-badge">Bramwell<br>Corner</div>
  <h1 class="hero-title">Welcome to<br>Bramwell Corner Sports<br>Pub</h1>
</header>

<section class="about">
  <h2 class="section-title">About Us</h2>
  <div class="about-art" role="img" aria-label="Pirate mascot raising a mug of beer with the pub name below"></div>
  <div class="text-block about-text">
    <p class="copy">Lorem ipsum dolor sit amet, consectetur adipiscing elit, sed do eiusmod tempor incididunt ut labore et dolore magna aliqua. Ut enim ad minim veniam, quis nostrud exercitation ullamco laboris nisi ut aliquip ex ea commodo consequat. Duis aute irure dolor in reprehenderit in voluptate velit esse cillum dolore eu fugiat nulla pariatur. Excepteur sint occaecat</p>
    <a class="btn btn-maroon" href="#">Read More</a>
  </div>
</section>

<section class="menu">
  <h2 class="section-title">Our Menu</h2>
  <p class="menu-intro">Lorem ipsum dolor sit amet, consectetur adipiscing elit, sed do eiusmod<br>tempor incididunt ut labore et dolore magna aliqua. Ut enim ad minim</p>
  <div class="menu-item" style="left:119px">
    <div class="menu-photo" role="img" aria-label="Lime cocktail splashing in a glass" style="background:radial-gradient(circle at 50% 55%,#8fb84a 0%,#3b4a1c 35%,#111 70%)"></div>
    <div class="menu-name">Lorem Ipsum</div>
    <div class="menu-price">$ 13.000</div>
  </div>
  <div class="menu-item" style="left:477px">
    <div class="menu-photo" role="img" aria-label="Glass of amber beer on a bar table" style="background:radial-gradient(circle at 55% 65%,#e08a22 0%,#8a4a1a 35%,#2e2a26 75%)"></div>
    <div class="menu-name">Lorem Ipsum</div>
    <div class="menu-price">$ 16.000</div>
  </div>
  <div class="menu-item" style="left:836px">
    <div class="menu-photo" role="img" aria-label="Red berry cocktail with ice and citrus" style="background:radial-gradient(circle at 55% 50%,#e23040 0%,#9a1420 40%,#3a0a0c 75%)"></div>
    <div class="menu-name">Lorem Ipsum</div>
    <div class="menu-price">$ 12.000</div>
  </div>
  <a class="btn btn-tan" href="#">View More</a>
</section>

<section class="events">
  <div class="barrel" role="img" aria-label="Faint wooden barrel decoration" style="left:-60px;top:10px;width:140px;height:250px"></div>
  <div class="barrel" role="img" aria-label="Faint wooden barrel decoration" style="left:1110px;top:630px;width:150px;height:250px"></div>
  <h2 class="section-title">Event</h2>
  <div class="event-photo" role="img" aria-label="Outdoor dinner table with salad and flowers" style="left:111px;top:214px;width:488px;height:305px;background:linear-gradient(160deg,#c9b27a 0%,#8a6a3a 40%,#a4483a 70%,#6b4a30 100%)"></div>
  <div class="text-block event-text" style="left:620px;top:218px;width:460px">
    <p class="copy">Lorem ipsum dolor sit amet, consectetur adipiscing elit, sed do eiusmod tempor incididunt ut labore et dolore magna aliqua. Ut enim ad minim veniam, quis nostrud exercitation ullamco laboris nisi ut aliquip ex ea commodo consequat. Duis</p>
    <a class="btn btn-tan" href="#">View More</a>
  </div>
  <div class="text-block event-text" style="left:131px;top:541px;width:455px">
    <p class="copy">Lorem ipsum dolor sit amet, consectetur adipiscing elit, sed do eiusmod tempor incididunt ut labore et dolore magna aliqua. Ut enim ad minim veniam, quis nostrud exercitation ullamco laboris nisi ut aliquip ex ea commodo consequat. Duis</p>
    <a class="btn btn-tan" href="#">View More</a>
  </div>
  <div class="event-photo" role="img" aria-label="Glasses of beer raised in a toast" style="left:599px;top:520px;width:490px;height:307px;background:radial-gradient(ellipse at 40% 55%,#d8902c 0%,#7a3e14 40%,#2a150a 85%)"></div>
</section>

<footer class="footer">
  <div class="footer-brand">Bramwell Corner</div>
  <nav class="footer-nav">
    <a href="#">Home</a><a href="#">About Us</a><a href="#">Services</a><a href="#">Event</a><a href="#">Contact Us</a><a href="#">FAQ</a>
  </nav>
  <div class="social" aria-label="Social links">
    <span aria-label="Social link 1"></span><span aria-label="Social link 2"></span><span aria-label="Social link 3"></span><span aria-label="Social link 4"></span>
  </div>
  <p class="legal">@2023 Copyrights Bramwell Corner Sports Pub Collection.<br>All Rights Reserved.</p>
</footer>

</body>
</html>
```